Executive Business Card for Healthcare Company [Need Today]

I need a business card design for a healthcare company. The only branding the company has thus far is a logo. The cards will be utilized by company executives. The design I envision will be vibrant and appealing but with a corporate feel. They shouldn't be too casual or playful. I would like to complete this project TODAY if possible.

Target Market(s)

Healthcare vendors, other executives in healthcare and pharmaceuticals

Industry/Entity Type

Pharmaceutical

Contact Information for Business Card

See attachment

Font styles to use
Serif
Sans Serif

Colors

Designer to choose colors to be used in the design.

```html
<!DOCTYPE html>
<html lang="en">
<head>
<meta charset="utf-8">
<title>Corvana Therapeutics – Executive Business Card</title>
<link href="https://fonts.googleapis.com/css2?family=Questrial&display=swap" rel="stylesheet">
<style>
  :root {
    --page-bg: #2b2b2d;
    --card-bg: #1b1b1c;
    --teal: #2cb8c4;
    --mint: #4fc79a;
    --text-light: #ececec;
    --text-muted: #bdbdbd;
    --divider-grey: #8a8a8a;
  }
  * { margin: 0; padding: 0; box-sizing: border-box; }
  html, body {
    width: 1200px; height: 1189px; overflow: hidden;
    background: var(--page-bg);
    font-family: "Questrial", "Century Gothic", sans-serif;
  }
  .card {
    position: absolute; left: 180px;
    width: 840px; height: 480px;
    background: var(--card-bg);
    border-radius: 28px;
    box-shadow: 0 18px 40px rgba(0,0,0,.45);
  }
  .card--front { top: 80px; }
  .card--back { top: 630px; }

  .brand { display: flex; align-items: center; gap: 18px; }
  .brand__mark {
    width: 118px; height: 118px; border-radius: 50%;
    border: 5px solid var(--mint); flex: none;
  }
  .brand__rule { width: 2px; height: 56px; background: var(--divider-grey); flex: none; }
  .brand__name {
    color: var(--teal); font-size: 38px; line-height: 1.05;
    letter-spacing: .5px; white-space: nowrap;
  }
  .brand__line { display: block; }

  .card--front .brand {
    position: absolute; left: 50%; top: 50%;
    transform: translate(-50%, -50%);
  }

  .card--back .brand { position: absolute; left: 56px; top: 172px; gap: 16px; }
  .card--back .brand__mark { width: 104px; height: 104px; }
  .card--back .brand__name { font-size: 32px; }

  .back__divider {
    position: absolute; left: 492px; top: 120px;
    width: 2px; height: 170px; background: var(--teal);
  }
  .contact { position: absolute; left: 522px; top: 126px; }
  .contact__name { color: var(--teal); font-size: 25px; font-weight: 700; letter-spacing: .3px; }
  .contact__title { color: var(--text-light); font-size: 18px; margin-top: 2px; }
  .contact__list { list-style: none; margin-top: 22px; }
  .contact__item {
    display: flex; align-items: center; gap: 10px;
    color: var(--text-light); font-size: 21px; line-height: 32px;
  }
  .contact__icon { width: 22px; height: 22px; flex: none; }

  .address {
    position: absolute; left: 0; right: 0; bottom: 62px;
    text-align: center; color: var(--text-light);
    font-size: 25px; letter-spacing: .6px;
  }
</style>
</head>
<body>

<section class="card card--front" aria-label="Card front">
  <div class="brand">
    <span class="brand__mark"></span>
    <span class="brand__rule"></span>
    <span class="brand__name"><span class="brand__line">Corvana</span><span class="brand__line">Therapeutics</span></span>
  </div>
</section>

<section class="card card--back" aria-label="Card back">
  <div class="brand">
    <span class="brand__mark"></span>
    <span class="brand__rule"></span>
    <span class="brand__name"><span class="brand__line">Corvana</span><span class="brand__line">Therapeutics</span></span>
  </div>

  <span class="back__divider"></span>

  <div class="contact">
    <p class="contact__name">Daniel Hart</p>
    <p class="contact__title">Senior Director of Marketing</p>
    <ul class="contact__list">
      <li class="contact__item">
        <svg class="contact__icon" viewBox="0 0 22 22" aria-hidden="true">
          <circle cx="11" cy="11" r="10" fill="none" stroke="var(--mint)" stroke-width="1.6"/>
          <rect x="7.5" y="5" width="7" height="12" rx="1.2" fill="none" stroke="var(--mint)" stroke-width="1.4"/>
          <line x1="10" y1="15" x2="12" y2="15" stroke="var(--mint)" stroke-width="1.2"/>
        </svg>
        555-210-4837
      </li>
      <li class="contact__item">
        <svg class="contact__icon" viewBox="0 0 22 22" aria-hidden="true">
          <circle cx="11" cy="11" r="10" fill="var(--mint)"/>
          <path d="M6 9c0-2 2-3 5-3s5 1 5 3l-2 .6-.6-1.6h-4.8L8 9.6z" fill="var(--card-bg)"/>
          <rect x="7" y="11" width="8" height="5" rx="1" fill="var(--card-bg)"/>
        </svg>
        555-730-1264
      </li>
      <li class="contact__item">
        <svg class="contact__icon" viewBox="0 0 22 22" aria-hidden="true">
          <circle cx="11" cy="11" r="10" fill="var(--mint)"/>
          <rect x="5.5" y="7" width="11" height="8" rx="1" fill="var(--card-bg)"/>
          <path d="M5.8 7.4 11 11.6l5.2-4.2" fill="none" stroke="var(--mint)" stroke-width="1.2"/>
        </svg>
        dhart@corvanarx.com
      </li>
    </ul>
  </div>

  <p class="address">118 Linden Avenue, Maplewood, GA 30999</p>
</section>

</body>
</html>
```